Defense Attorney Business Card Design Project/ Stationary

I am looking for a distinctive business card design for my solo law practice.
I practice criminal defense, both juvenile and adult, including DUI. I am a very experienced attorney with prior military experience. The design should convey a traditional, old school flair, but not be too stodgy or uptight. Some color. My logo should appear.
Updates

Project Deadline Extended Reason: I misunderstood how this project works and I was not prepared with my logo when this project ran the first time. Added Thursday, November 13, 2014

Project Deadline Extended
Reason: I was sent overseas on military duty last year, which interrupted this project. Thank you for your participation... I hope we can get this done this week! Thank you, Neil

Target Market(s)

Regular everyday people looking for strong, knowledgeable, authoritative representation while they are faced with criminal charges. Many have never been charged with a crime before. A reassuring air is therefore desired.

Industry/Entity Type

Business

Contact Information for Business Card

My information is:
Theodore M. Quill, Attorney at Law
785 Birch Avenue Suite 300
Oakland, California 94719
Tel: (510) 384-6125
Fax: (510) 391-7802
email: neilquilllaw@mailvine.example
web: www.neilquilllaw.example

Font styles to use
Serif
Sans Serif
Decorative

Colors
0255a3
ffffff

Requirements
Must have
• Sharp lines, bold elements. Conservative use of colors, such as deep blues, burgundy, grays for example.
• While my logo says "Theodore M. Quill", it should be modified to show "Theodore M. Quill".
Should not have
• Cliche imagery such as scales of justice, gavels, Statue of Liberty, etc.

```html
<!DOCTYPE html>
<html lang="en">
<head>
<meta charset="utf-8">
<title>Theodore M. Quill Law — Business Cards</title>
<link rel="stylesheet" href="https://fonts.googleapis.com/css2?family=Cardo&family=Cinzel&display=swap">
<style>
  :root {
    --law-blue: #0255a3;
    --paper: #ffffff;
    --backdrop: #e9eaec;
    --card-shadow: rgba(20, 30, 50, 0.18);
  }
  * { box-sizing: border-box; margin: 0; padding: 0; }
  html, body { width: 1200px; height: 1000px; overflow: hidden; }
  body {
    background: var(--backdrop);
    font-family: "Cardo", "Times New Roman", serif;
    color: var(--law-blue);
    position: relative;
  }
  .card {
    position: absolute;
    top: 345px;
    width: 525px;
    height: 300px;
    box-shadow: 0 6px 18px var(--card-shadow);
    overflow: hidden;
  }

  /* Front of card */
  .card-front { left: 50px; background: var(--paper); }
  .rule { position: absolute; background: var(--law-blue); }
  .rule-horizontal { left: 0; right: 0; top: 62px; height: 2px; }
  .rule-vertical { left: 200px; top: 0; bottom: 0; width: 2px; }

  .firm-mark {
    position: absolute;
    left: 0; top: 64px; width: 200px; height: 236px;
    padding: 0 16px;
    display: flex; align-items: center; justify-content: center; gap: 8px;
  }
  .firm-mark .mark-square { flex: none; width: 10px; height: 10px; background: var(--law-blue); }
  .firm-name {
    font-family: "Cinzel", "Times New Roman", serif;
    font-size: 15px;
    line-height: 1.3;
    letter-spacing: 0.4px;
    color: var(--law-blue);
  }

  .name-plate {
    position: absolute;
    left: 120px; top: 45px;
    padding: 4px 14px;
    background: var(--paper);
    border: 2px solid var(--law-blue);
    font-size: 19px;
    line-height: 1.3;
    white-space: nowrap;
  }

  .contact {
    position: absolute;
    right: 28px;
    top: 120px;
    text-align: right;
    font-size: 12.5px;
    line-height: 1.35;
  }
  .contact .address { margin-bottom: 16px; }

  /* Back of card */
  .card-back { left: 625px; background: var(--law-blue); }
  .back-frame {
    position: absolute;
    left: 44px; right: 44px; top: 32px; bottom: 32px;
    border: 2px solid var(--paper);
    display: flex; align-items: center; justify-content: center; gap: 12px;
  }
  .back-frame .mark-circle {
    flex: none; width: 14px; height: 14px; border-radius: 50%; background: var(--paper);
  }
  .back-frame .firm-name { color: var(--paper); font-size: 25px; white-space: nowrap; }
  .edge-stripes {
    position: absolute; top: 0; bottom: 0; width: 10px;
    border-left: 2px solid var(--paper);
    border-right: 2px solid var(--paper);
  }
  .edge-stripes-left { left: 18px; }
  .edge-stripes-right { right: 18px; }
</style>
</head>
<body>

  <section class="card card-front" aria-label="Business card front">
    <div class="rule rule-horizontal"></div>
    <div class="rule rule-vertical"></div>

    <div class="firm-mark">
      <span class="mark-square"></span>
      <span class="firm-name">Theodore M. Quill Law</span>
    </div>

    <div class="name-plate">Theodore M. Quill, Attorney at Law</div>

    <div class="contact">
      <p class="address">785 Birch Avenue Suite 300<br>Oakland, California 94719</p>
      <p>Tel: (510) 384-6125</p>
      <p>Fax: (510) 391-7802</p>
      <p>Website: www.neilquilllaw.example</p>
      <p>Email: neilquilllaw@mailvine.example</p>
    </div>
  </section>

  <section class="card card-back" aria-label="Business card back">
    <div class="edge-stripes edge-stripes-left"></div>
    <div class="edge-stripes edge-stripes-right"></div>
    <div class="back-frame">
      <span class="mark-circle"></span>
      <span class="firm-name">Theodore M. Quill Law</span>
    </div>
  </section>

</body>
</html>
```